Verdo Consultants Exhibition Booth Design. Cannabis Legal Consultancy

We require a design for the following artwork in PDF of Jpeg high resolution format with these specifications, a 5cm bleed outside and a 10cm safe inside bleed. A tension fabric backdrop 200cm wide and 231cm high. (example loaded) Please see our website www.theverdoconsultants.co.uk
Attached are company logos and head shots for inclusion. You will see our colour schemes from the website. It should announce who we are and provide the company website.

```html
<!DOCTYPE html>
<html lang="en">
<head>
<meta charset="utf-8">
<title>Verdo Consultants – Exhibition Backdrop</title>
<link rel="stylesheet" href="https://fonts.googleapis.com/css2?family=League+Gothic&family=Montserrat:wght@500;600&display=swap">
<style>
  :root {
    --blue: #1652f0;
    --charcoal: #3f4443;
    --ink: #353a39;
    --paper: #ffffff;
    --stage: #e4e8e8;
    --photo-dark: #2b3335;
    --photo-mid: #617174;
    --portrait-light: #a3a9ab;
  }
  * { margin: 0; padding: 0; box-sizing: border-box; }
  html, body { width: 1200px; height: 977px; overflow: hidden; background: var(--stage); }
  .backdrop {
    position: absolute; left: 210px; top: 38px;
    width: 780px; height: 900px;
    background: var(--paper); overflow: hidden;
  }
  .backdrop-shapes { position: absolute; inset: 0; }
  .stroke-grey { fill: none; stroke: var(--charcoal); }
  .stroke-blue { fill: none; stroke: var(--blue); }
  .fill-paper { fill: var(--paper); }
  .fill-blue { fill: var(--blue); }
  .fill-charcoal { fill: var(--charcoal); }
  .photo-dark { fill: var(--photo-dark); }
  .photo-light { fill: var(--portrait-light); }

  .brand {
    position: absolute; left: 495px; top: 52px;
    font-family: "Montserrat", sans-serif; font-weight: 600;
    color: var(--blue); line-height: 1;
  }
  .brand-the { display: block; font-size: 24px; font-weight: 500; color: var(--charcoal); }
  .brand-name { display: block; font-size: 32px; margin-top: 6px; line-height: 1.08; }
  .brand-url { display: block; font-size: 12px; font-weight: 500; color: var(--ink); margin-top: 6px; }

  .services {
    position: absolute; right: 22px; top: 210px; text-align: right;
    font-family: "League Gothic", sans-serif; font-weight: 400;
    color: var(--blue); font-size: 70px; line-height: 60px;
    text-transform: uppercase;
  }
  .tagline {
    position: absolute; right: 22px; top: 392px; text-align: right;
    font-family: "Montserrat", sans-serif; font-weight: 600;
    color: var(--ink); font-size: 30px; line-height: 42px;
  }
  .name-pill {
    position: absolute; height: 38px; border-radius: 19px;
    background: var(--blue); color: var(--paper);
    font-family: "League Gothic", sans-serif; font-size: 30px; line-height: 1;
    display: flex; align-items: center; justify-content: center;
    text-transform: uppercase; letter-spacing: 0.3px;
  }
  .name-pill--left { left: 52px; top: 786px; width: 204px; }
  .name-pill--right { left: 330px; top: 692px; width: 180px; }
  .footer-url {
    position: absolute; right: 22px; top: 818px;
    font-family: "League Gothic", sans-serif;
    color: var(--paper); font-size: 48px; line-height: 1;
  }
</style>
</head>
<body>
<main class="backdrop">
  <svg class="backdrop-shapes" width="780" height="900" viewBox="0 0 780 900">
    <defs>
      <radialGradient id="compass-tone" cx="0.6" cy="0.35" r="0.7">
        <stop offset="0" stop-color="#617174"/>
        <stop offset="1" stop-color="#2b3335"/>
      </radialGradient>
    </defs>

    <path class="stroke-grey" d="M 107 14 A 345 345 0 0 1 293 621" stroke-width="7"/>
    <path class="stroke-blue" d="M -10 48 A 318 318 0 0 1 305 188" stroke-width="12"/>
    <path class="stroke-blue" d="M -10 662 A 318 318 0 0 0 60 690" stroke-width="10"/>
    <circle class="stroke-grey" cx="71" cy="357" r="276" stroke-width="18"/>
    <circle cx="71" cy="357" r="264" fill="url(#compass-tone)" role="img" aria-label="Photo of a compass with its needle pointing to the word answers"/>

    <circle class="stroke-blue" cx="425" cy="100" r="55" stroke-width="4"/>

    <line class="stroke-blue" x1="545" y1="484" x2="758" y2="488" stroke-width="1"/>
    <rect class="fill-charcoal" x="618" y="478" width="11" height="14"/>

    <circle class="fill-paper stroke-grey" cx="411" cy="537" r="114" stroke-width="5" style="fill:#fff"/>
    <path class="stroke-blue" d="M 411 441 A 96 96 0 1 0 495 583" stroke-width="4"/>
    <circle class="stroke-grey" cx="411" cy="537" r="84" stroke-width="4"/>
    <circle class="photo-light" cx="411" cy="537" r="80" role="img" aria-label="Headshot of Chris Morley"/>

    <circle class="stroke-grey" cx="156" cy="634" r="140" stroke-width="5" style="fill:#fff"/>
    <path class="stroke-blue" d="M 156 518 A 116 116 0 1 0 266 598" stroke-width="4"/>
    <circle class="stroke-grey" cx="156" cy="634" r="102" stroke-width="4"/>
    <circle class="photo-dark" cx="156" cy="634" r="98" role="img" aria-label="Headshot of Daniel Hart"/>

    <circle class="stroke-grey" cx="600" cy="1137" r="414" stroke-width="12"/>
    <circle class="fill-blue" cx="600" cy="1137" r="398"/>
  </svg>

  <div class="brand">
    <span class="brand-the">THE</span>
    <span class="brand-name">VERDO<br>CONSULTANTS</span>
    <span class="brand-url">www.theverdoconsultants.co.uk</span>
  </div>

  <h1 class="services">Assessment<br>Advice<br>Implementation</h1>

  <p class="tagline">Be Careful Who<br>You Listen To</p>

  <div class="name-pill name-pill--right">Chris Morley</div>
  <div class="name-pill name-pill--left">Daniel Hart</div>

  <p class="footer-url">www.theverdoconsultants.co.uk</p>
</main>
</body>
</html>
```